Young, dynamic furniture company needs a new business card design

We require a new business card design for our modern furniture company which supplies furniture and appliances to the property and development market.
Oakridge Interiors has become one of the leading furniture & appliance suppliers to the property market withing London. With over 10 years experience, we have increased our business to supply not only private landlords and managing agents, but also property developers, housing associations and local councils.
We offer not only a complete range of furniture which includes beds, wardrobes, dining sets and sofas, but also a high quality, full delivery and assembly service to help you with all our furnishing needs.

Target Market(s)

Private landlords, estate agents, letting agents, property management companies

Industry/Entity Type

Business

Contact Information for Business Card

Name,
Title,
Address,
Mobile,
Telephone,
Fax, Website, email address

Font styles to use
Sans Serif

Colors
3176b5
0555a3
85abd2
cfdeed

Requirements
Must have
• All the above information for each of our staff, along with our logo

```html
<!DOCTYPE html>
<html lang="en">
<head>
<meta charset="utf-8">
<title>Oakridge Interiors — Business Card</title>
<link href="https://fonts.googleapis.com/css2?family=Lato:wght@400;700&display=swap" rel="stylesheet">
<style>
  :root {
    --blue-mid: #3176b5;
    --blue-deep: #0555a3;
    --blue-soft: #85abd2;
    --blue-pale: #cfdeed;
    --ink: #111418;
    --paper: #ffffff;
    --stage: #e6e8eb;
  }
  * { box-sizing: border-box; margin: 0; padding: 0; }
  html, body {
    width: 1200px; height: 900px; overflow: hidden;
    background: var(--stage);
    font-family: "Lato", sans-serif;
  }
  .canvas { position: relative; width: 1200px; height: 900px; }

  .card {
    position: absolute;
    width: 700px; height: 400px;
    overflow: hidden;
    box-shadow: 0 6px 18px rgba(0,0,0,0.18);
  }

  /* Front face */
  .card--front {
    left: 440px; top: 50px;
    background: var(--blue-deep);
    color: var(--paper);
    display: flex; flex-direction: column; align-items: center; justify-content: center;
    text-align: center;
  }
  .brand { display: flex; flex-direction: column; align-items: center; }
  .brand__row { display: flex; align-items: center; gap: 14px; }
  .brand__square { width: 26px; height: 26px; flex: none; }
  .card--front .brand__square { background: var(--paper); }
  .brand__name {
    font-weight: 400; font-size: 38px; letter-spacing: 1px; text-transform: uppercase;
    white-space: nowrap;
  }
  .brand__tagline {
    font-size: 16px; letter-spacing: 1.5px; text-transform: uppercase; margin-top: 4px;
    white-space: nowrap;
  }
  .card--front .brand__name { color: var(--paper); }
  .card--front .brand__tagline { color: var(--blue-pale); }
  .front-web {
    margin-top: 30px; font-size: 20px; letter-spacing: 3px;
  }

  /* Back face */
  .card--back {
    left: 70px; top: 470px;
    background: var(--paper);
  }
  .card__waves { position: absolute; inset: 0; width: 100%; height: 100%; }
  .details {
    position: absolute; left: 56px; top: 78px;
    color: var(--ink);
  }
  .details__name { color: var(--blue-mid); font-size: 30px; font-weight: 400; }
  .details__title { font-size: 17px; margin: 2px 0 14px; }
  .details__address { font-size: 17px; line-height: 1.35; margin-bottom: 10px; }
  .contact { list-style: none; font-size: 17px; line-height: 1.4; }
  .contact li { display: flex; align-items: center; gap: 10px; }
  .contact svg { width: 14px; height: 14px; fill: var(--blue-mid); flex: none; }

  .card--back .brand {
    position: absolute; right: 40px; top: 140px; align-items: flex-start;
  }
  .card--back .brand__square { background: var(--blue-mid); width: 22px; height: 22px; }
  .card--back .brand__row { gap: 12px; }
  .card--back .brand__name { color: var(--ink); font-size: 28px; }
  .card--back .brand__tagline { color: var(--ink); font-size: 13px; margin-left: 34px; }
</style>
</head>
<body>
<main class="canvas">

  <section class="card card--front" aria-label="Card front">
    <div class="brand">
      <div class="brand__row">
        <span class="brand__square"></span>
        <span class="brand__name">Oakridge Interiors</span>
      </div>
      <span class="brand__tagline">Trade Furniture Solutions</span>
    </div>
    <p class="front-web">www.trade.oakridge.co.uk</p>
  </section>

  <section class="card card--back" aria-label="Card back">
    <svg class="card__waves" viewBox="0 0 700 400" preserveAspectRatio="none" aria-hidden="true">
      <path d="M0 0 H420 Q200 20 0 70 Z" fill="var(--blue-mid)"/>
      <path d="M0 70 Q200 20 420 0 L440 0 Q220 35 0 95 Z" fill="var(--blue-soft)"/>
      <path d="M0 95 Q220 35 440 0 L448 0 Q225 42 0 102 Z" fill="var(--paper)"/>
      <path d="M140 400 Q470 345 700 262 V292 Q520 368 250 400 Z" fill="var(--blue-soft)"/>
      <path d="M250 400 Q520 368 700 292 V300 Q525 374 275 400 Z" fill="var(--paper)"/>
      <path d="M275 400 Q525 374 700 300 V400 Z" fill="var(--blue-mid)"/>
    </svg>

    <div class="details">
      <h1 class="details__name">Daniel Hartley</h1>
      <p class="details__title">Manager</p>
      <p class="details__address">27B Alder Trade Park<br>North Finchley, London</p>
      <ul class="contact">
        <li><svg viewBox="0 0 24 24"><path d="M6.6 10.8a15 15 0 006.6 6.6l2.2-2.2c.3-.3.7-.4 1-.2 1.1.4 2.3.6 3.6.6.6 0 1 .4 1 1V20c0 .6-.4 1-1 1A17 17 0 013 4c0-.6.4-1 1-1h3.5c.6 0 1 .4 1 1 0 1.3.2 2.5.6 3.6.1.3 0 .7-.2 1z"/></svg>020 7946 0321</li>
        <li><svg viewBox="0 0 24 24"><path d="M7 1h10a2 2 0 012 2v18a2 2 0 01-2 2H7a2 2 0 01-2-2V3a2 2 0 012-2zm0 4v13h10V5z"/></svg>020 7946 0500</li>
        <li><svg viewBox="0 0 24 24"><path d="M2 5h20v14H2zm2 2v.5l8 5 8-5V7z"/></svg>info@trade.oakridge.co.uk</li>
        <li><svg viewBox="0 0 24 24"><path d="M12 2a10 10 0 100 20 10 10 0 000-20zm0 2c1.2 1.4 2 3.6 2.2 7H9.8c.2-3.4 1-5.6 2.2-7zM4.1 11a8 8 0 014-6.2A13 13 0 007.8 11zm0 2h3.7c.1 2.4.6 4.6 1.3 6.2A8 8 0 014.1 13zm5.7 0h4.4c-.2 3.4-1 5.6-2.2 7-1.2-1.4-2-3.6-2.2-7zm6.4 0h3.7a8 8 0 01-4 6.2c.7-1.6 1.2-3.800 1.3-6.2zm0-2a13 13 0 00-.3-6.2 8 8 0 014 6.2z"/></svg>www.trade.oakridge.co.uk</li>
      </ul>
    </div>

    <div class="brand">
      <div class="brand__row">
        <span class="brand__square"></span>
        <span class="brand__name">Oakridge Interiors</span>
      </div>
      <span class="brand__tagline">Trade Furniture Solutions</span>
    </div>
  </section>

</main>
</body>
</html>
```